Etiketten für Bio Seifen
Zielgruppe
Wir stellen hochwertig 'handgemachte' Bio-Seifen her. Die Zielgruppe ist von 3-99 Jahren und zusätzlich haben wir auch noch Seife für Hunde.
Der Firmenname ist 'Verdolina'
Aufgabenstellung
Das Etikett soll Bezug auf Natur, Bio, Nachhaltigkeit nehmen. Wir stellen uns 'weiche' Aquarellfarben vor...Seife: Lavendel, Calendular, 7 Kräuter etc.
Das Etikett soll auf eine Beutelschachtel. Die Schachtel hat eine Anmaße: Breite 55mm; Höhe 120mm; Tiefe 30mm
Das Etikett soll im vorderen- und hinteren Bereich zusammenhängend geklebt werden.
Das Etikett soll eine Abmaße von: Breite 51mm; Höhe 114mm haben (Vorderseite) Rückseite gleich.
Wir möchten die Produkte auch gerne nummerieren, d.h. jede Seife hat eine Nummer die nicht zu groß dargestellt werden soll aber trotzdem gut leserlich.
Wir haben noch ein paar Bilder hochgeladen wie wir uns das ungefähr vorstellen.

```html
<!DOCTYPE html>
<html lang="de">
<head>
<meta charset="utf-8">
<title>Verdolina – Etiketten Bioseife</title>
<link href="https://fonts.googleapis.com/css2?family=Montserrat:wght@400;500&family=Playfair+Display:ital,wght@1,400;1,700&family=Great+Vibes&display=swap" rel="stylesheet">
<style>
  :root {
    --navy: #0d3e6f;
    --paper: #ffffff;
    --edge: #c9c9c9;
    --lavender: #a79fcb;
    --lavender-deep: #6e4f9c;
    --lavender-soft: #e6e1f1;
    --calendula: #f0a31f;
    --calendula-deep: #e88a2a;
    --calendula-soft: #fbe2b0;
    --herb: #5cb37f;
    --herb-deep: #1f8a4c;
    --herb-soft: #e4f2e8;
  }
  * { box-sizing: border-box; margin: 0; padding: 0; }
  html, body { width: 1200px; height: 782px; overflow: hidden; background: var(--paper); }
  .sheet { position: relative; width: 1200px; height: 782px; }

  .label {
    position: absolute; top: 21px; width: 338px; height: 736px;
    border: 1px solid var(--edge); background: var(--paper);
  }
  .label--lavendel { left: 20px; --accent: var(--lavender); --deep: var(--lavender-deep); --soft: var(--lavender-soft); }
  .label--calendula { left: 431px; --accent: var(--calendula); --deep: var(--calendula-deep); --soft: var(--calendula-soft); }
  .label--kraeuter { left: 842px; --accent: var(--herb); --deep: var(--herb-deep); --soft: var(--herb-soft); }

  .brand-name {
    position: absolute; left: 0; right: 0; top: 120px;
    display: flex; align-items: center; justify-content: center; gap: 10px;
    font-family: "Montserrat", sans-serif; font-weight: 500; font-size: 38px;
    letter-spacing: 1px; color: var(--navy); line-height: 1;
  }
  .brand-dot { width: 16px; height: 16px; border-radius: 50%; background: var(--accent); }
  .tagline {
    position: absolute; left: 0; right: 0; top: 186px; text-align: center;
    font-family: "Playfair Display", serif; font-style: italic; font-size: 16px; color: var(--navy);
  }
  .category {
    position: absolute; left: 55px; top: 237px; width: 227px; height: 28px;
    background: var(--accent); color: var(--navy);
    font-family: "Montserrat", sans-serif; font-size: 13.5px; letter-spacing: 0.6px;
    display: flex; align-items: center; justify-content: center;
  }
  .artwork {
    position: absolute; left: 15px; top: 306px; width: 308px; height: 351px;
    background:
      radial-gradient(ellipse at 20% 15%, var(--deep) 0%, transparent 60%),
      radial-gradient(ellipse at 85% 85%, var(--accent) 0%, transparent 55%),
      linear-gradient(135deg, var(--accent) 0%, var(--soft) 100%);
  }
  .nameplate {
    position: absolute; left: 56px; top: 553px; width: 226px; height: 77px;
    background: var(--paper); border: 2px solid var(--navy);
    outline: 1px solid var(--navy); outline-offset: -5px;
    text-align: center; color: var(--navy);
  }
  .nameplate__number {
    display: block; margin-top: 13px;
    font-family: "Montserrat", sans-serif; font-size: 16px; letter-spacing: 0.5px;
  }
  .nameplate__title {
    display: block; margin-top: 2px;
    font-family: "Playfair Display", serif; font-style: italic; font-weight: 700;
    font-size: 21px; letter-spacing: 1px;
  }
  .benefit {
    position: absolute; left: 15px; top: 657px; width: 308px; height: 48px;
    background: var(--navy); color: var(--paper);
    font-family: "Great Vibes", cursive; font-size: 24px;
    display: flex; align-items: center; justify-content: center;
  }
</style>
</head>
<body>
<main class="sheet">

  <section class="label label--lavendel">
    <div class="brand-name"><span class="brand-dot"></span>Verdolina</div>
    <p class="tagline">Natur auf der Haut</p>
    <div class="category">HANDGEMACHTE BIOSEIFE</div>
    <div class="artwork" role="img" aria-label="Aquarell in Lila mit weiß gezeichneten Blüten"></div>
    <div class="nameplate"><span class="nameplate__number">N°1</span><span class="nameplate__title">LAVENDEL</span></div>
    <div class="benefit">beruhigend &amp; entspannend</div>
  </section>

  <section class="label label--calendula">
    <div class="brand-name"><span class="brand-dot"></span>Verdolina</div>
    <p class="tagline">Natur auf der Haut</p>
    <div class="category">HANDGEMACHTE BIOSEIFE</div>
    <div class="artwork" role="img" aria-label="Aquarell in Orange und Gelb mit weiß gezeichneten Blüten"></div>
    <div class="nameplate"><span class="nameplate__number">N°2</span><span class="nameplate__title">CALENDULA</span></div>
    <div class="benefit">mild reinigend &amp; sanft pflegend</div>
  </section>

  <section class="label label--kraeuter">
    <div class="brand-name"><span class="brand-dot"></span>Verdolina</div>
    <p class="tagline">Natur auf der Haut</p>
    <div class="category">HANDGEMACHTE BIOSEIFE</div>
    <div class="artwork" role="img" aria-label="Aquarell in Grün mit weiß gezeichneten Blüten"></div>
    <div class="nameplate"><span class="nameplate__number">N°3</span><span class="nameplate__title">7 KRÄUTER</span></div>
    <div class="benefit">nährend &amp; beruhigend</div>
  </section>

</main>
</body>
</html>
```